upmarket Hair salon A5 flyer design colour double sided

Phone number 8317 6091
address is shop 3/8 Marrowgate blvd Butler
Hi i am wanting a flyer that is upmarket and elegant for my hair salon Velvet Lockz For Hair if any pics of hair must look great.
both side must have logo and contact details on
offer side 1
50% off
style cut and finish
*not valid Saturdays
*expires 31/03/15
*butler salon only
*not valid with any other offers
offer side 2
1/2 head foils or all over colour,
cut and finish
$120
*toners and treatment extra costs
*expires 31/03/15
*butler salon only

```html
<!DOCTYPE html>
<html lang="en">
<head>
<meta charset="utf-8">
<title>Velvet Lockz For Hair – Offer Flyer</title>
<link rel="stylesheet" href="https://fonts.googleapis.com/css2?family=Oswald:wght@300;400&family=Playfair+Display:wght@400&display=swap">
<style>
  :root {
    --paper: #f4f4f5;
    --paper-edge: #dcdcdf;
    --ink: #1d1d1f;
    --ink-soft: #3a3a3d;
    --navy: #22318c;
    --violet: #7b6fc2;
    --teal: #9fcbd3;
    --rule: #8a8a8f;
    --tab: #ffffff;
  }
  * { margin: 0; padding: 0; box-sizing: border-box; }
  html, body { width: 855px; height: 1200px; overflow: hidden; }
  body { background: var(--paper); font-family: "Oswald", "Arial Narrow", sans-serif; color: var(--ink); }

  .flyer {
    position: relative;
    width: 855px;
    height: 1200px;
    overflow: hidden;
    background: radial-gradient(ellipse at 50% 65%, #ffffff 0%, var(--paper) 55%, var(--paper-edge) 100%);
  }

  .flourish {
    position: absolute;
    left: 0; top: 0;
    width: 855px; height: 700px;
  }

  .brand-tab {
    position: absolute;
    left: -20px; top: 28px;
    width: 335px; height: 155px;
    background: var(--tab);
    border-radius: 0 32px 32px 0;
    box-shadow: 0 4px 14px rgba(0,0,0,.18);
    display: flex;
    flex-direction: column;
    justify-content: center;
    padding-left: 52px;
  }
  .brand-name {
    font-family: "Oswald", "Arial Narrow", sans-serif;
    font-weight: 300;
    font-size: 40px;
    line-height: 1.05;
    color: var(--ink-soft);
    letter-spacing: 0.5px;
  }

  .offer-title {
    position: absolute;
    top: 595px; left: 0; width: 100%;
    text-align: center;
    font-family: "Playfair Display", Georgia, serif;
    font-weight: 400;
    font-size: 96px;
    line-height: 1;
    color: var(--ink);
  }

  .offer-detail {
    position: absolute;
    top: 720px; left: 0; width: 100%;
    text-align: center;
    font-weight: 300;
    font-size: 42px;
    line-height: 1.2;
    color: var(--ink);
  }

  .terms {
    position: absolute;
    top: 905px; left: 0; width: 100%;
    text-align: center;
    font-weight: 300;
    font-size: 18px;
    line-height: 1.45;
    color: var(--ink-soft);
  }
  .terms span { margin: 0 6px; }

  .divider {
    position: absolute;
    top: 1040px; left: 130px;
    width: 595px; height: 30px;
  }

  .contact {
    position: absolute;
    top: 1078px; left: 0; width: 100%;
    text-align: center;
    font-weight: 300;
    font-size: 20px;
    line-height: 2;
    color: var(--ink-soft);
  }
</style>
</head>
<body>
<main class="flyer">

  <svg class="flourish" viewBox="0 0 855 700" role="img" aria-label="Ornamental swirling floral vines in navy, violet and soft teal across the top of the flyer">
    <defs>
      <linearGradient id="flourishTone" x1="0" y1="0" x2="1" y2="1">
        <stop offset="0" stop-color="#9fcbd3" stop-opacity="0.55"/>
        <stop offset="0.45" stop-color="#7b6fc2" stop-opacity="0.5"/>
        <stop offset="1" stop-color="#22318c" stop-opacity="0.45"/>
      </linearGradient>
    </defs>
    <path d="M0 0 H855 V700 C820 640 790 600 760 560 C700 520 640 560 580 520 C520 480 470 560 420 540 C360 520 320 470 270 500 C220 530 170 480 120 500 C80 515 40 470 0 480 Z" fill="url(#flourishTone)"/>
  </svg>

  <div class="brand-tab">
    <div class="brand-name">Velvet Lockz<br>For Hair</div>
  </div>

  <h1 class="offer-title">offer</h1>

  <p class="offer-detail">1/2 head foils or all over colour,<br>cut and finish<br>$120</p>

  <p class="terms">
    <span>*toners and treatment extra costs</span><span>*expires 31/03/15</span><span>*butler salon only</span><br>
    <span>*not valid with any other offers</span>
  </p>

  <svg class="divider" viewBox="0 0 595 30" aria-hidden="true">
    <line x1="0" y1="15" x2="270" y2="15" stroke="var(--rule)" stroke-width="1.5"/>
    <circle cx="297.5" cy="15" r="8" fill="var(--teal)"/>
    <line x1="325" y1="15" x2="595" y2="15" stroke="var(--rule)" stroke-width="1.5"/>
  </svg>

  <address class="contact" style="font-style:normal">
    ph 8317 6091<br>
    shop 3/8 Marrowgate blvd Butler
  </address>

</main>
</body>
</html>
```